Website design with eCommerce for revolutionary new product in the manufacturing industry.

We need a website designed for a precision manufacturing company based in the suburbs of Minneapolis, Minnesota called Velkrin Manufacturing. We have a revolutionary new product, the TARN LOCK, to introduce and sell through an eCommerce storefront. The website would include company information, product information, and the storefront. Green is a color that represents Velkrin Manufacturing. The final design should communicate that we exclusively offer premium products at a premium price. The design should also let the customer know they are the focus of our work.

Target Market(s)

Machinists and machine shops

Industry/Entity Type

Manufacturing and machine shops

Coding

Coded - Design and coding required

Font styles to use
Sans Serif

Colors
59FF00
82FF00
B8FF75
E3FFCB
F4FFEA

Requirements
Must have
• eCommerce storefront, Made in USA references
Nice to have
• Home page, TARN LOCK Product page, About Us, Capabilities, Contact, etc.
Should not have
• Should not be too much text and reading.

```html
<!DOCTYPE html>
<html lang="en">
<head>
<meta charset="utf-8">
<title>Velkrin Manufacturing – Website</title>
<link href="https://fonts.googleapis.com/css2?family=Poppins:wght@400;600;800&family=Open+Sans:wght@400;600&display=swap" rel="stylesheet">
<style>
:root{
  --green:#59ff00;
  --lime:#82ff00;
  --mint:#b8ff75;
  --pale:#e3ffcb;
  --ink:#161616;
  --char:#222;
  --paper:#fff;
  --board:#e9eaeb;
}
*{box-sizing:border-box;margin:0;padding:0}
html,body{width:1200px;height:2684px;overflow:hidden}
body{background:var(--board);font-family:"Open Sans",Arial,sans-serif;color:var(--ink);position:relative}
h1,h2,h3,.brand,.btn,.callbox{font-family:"Poppins",Arial,sans-serif}
.page{position:absolute;background:var(--paper);overflow:hidden;box-shadow:0 6px 24px rgba(0,0,0,.18)}
.page-home{left:168px;top:412px;width:376px;height:1672px}
.page-gallery{left:624px;top:112px;width:376px;height:648px}
.page-product{left:624px;top:820px;width:376px;height:920px}
.page-contact{left:624px;top:1772px;width:376px;height:708px}
.sec{position:absolute;left:0;width:100%}
.photo{position:absolute}
.ph-dark{background:linear-gradient(135deg,#2c2f32,#0d0e0f 60%,#3b3f43)}
.ph-metal{background:linear-gradient(135deg,#9b8a6a,#d7d2c8 40%,#6e6a63)}
.ph-steel{background:linear-gradient(135deg,#6d7176,#c9ccd0 50%,#4a4d51)}
.ph-gold{background:linear-gradient(135deg,#a8773a,#e3b46a 50%,#6f4c22)}
.ph-map{background:linear-gradient(135deg,#dcdde0,#f2f2f3 50%,#cfd1d4)}
.ph-green{background:linear-gradient(135deg,#2a2d30,#59ff00 55%,#2f8f00)}
.nav{position:absolute;top:0;left:0;width:100%;height:20px;background:var(--paper);display:flex;align-items:center;padding:0 8px;gap:8px;z-index:3}
.brand{font-weight:800;font-size:7px;color:var(--ink);display:flex;align-items:center;gap:3px;white-space:nowrap}
.brand i{width:6px;height:6px;background:var(--green);display:inline-block}
.nav ul{list-style:none;display:flex;gap:7px;font-size:4.5px;color:#444;margin-left:auto}
.nav .btn{background:var(--green);color:var(--ink);font-size:4.5px;padding:3px 6px}
.btn{display:inline-block;background:var(--ink);color:#fff;font-size:5px;font-weight:600;padding:4px 10px}
.btn-green{background:var(--green);color:var(--ink)}
h2{font-size:11px;font-weight:800;text-transform:uppercase;line-height:1.15}
h2 em{font-style:normal;color:var(--green)}
.center{position:absolute;width:100%;text-align:center}
p{font-size:5px;line-height:1.6;color:#555}
.dark p{color:#bbb}
.hero{top:20px;height:180px}
.hero-title{position:absolute;left:104px;top:30px;width:168px;height:96px;border:2px solid #fff;text-align:center;color:#fff;padding-top:14px}
.hero-title h1{font-size:14px;font-weight:800;line-height:1.05}
.hero-title h1 span{display:block;color:var(--green);font-size:28px}
.slant{position:absolute;left:0}
.card{width:78px;height:92px;background:#fff;box-shadow:0 2px 8px rgba(0,0,0,.12);padding:8px}
.card b{display:block;width:12px;height:12px;border:1.5px solid var(--green);margin-bottom:6px}
.card strong{display:block;font-size:5.5px;color:var(--ink);margin-bottom:2px}
.cap{display:flex;gap:5px;align-items:center;color:#fff;font-size:5px;font-weight:600}
.cap b{width:14px;height:14px;background:var(--green);flex:none}
.thumbs{position:absolute;left:20px;right:20px;display:grid;gap:6px}
.spec{display:flex;gap:4px;align-items:flex-start;margin-bottom:5px}
.spec b{width:5px;height:5px;background:var(--green);flex:none;margin-top:2px}
.row{position:absolute;left:0;width:100%}
.price{font-family:"Poppins",sans-serif;font-weight:800;font-size:12px;margin:4px 0 6px}
.footer{position:absolute;left:0;width:100%;background:var(--ink);color:#ddd}
.foot-cols{position:absolute;left:16px;right:16px;top:34px;display:flex;gap:12px}
.foot-cols>div{flex:1;font-size:4.6px;line-height:1.9;color:#aaa}
.foot-cols h3{font-size:5.4px;color:#fff;margin-bottom:3px;letter-spacing:.3px}
.foot-cols p{font-size:4.6px;color:#aaa;margin-top:5px}
.field{height:10px;background:#333;margin:3px 0}
.send{display:inline-block;background:var(--green);color:var(--ink);font-family:"Poppins",sans-serif;font-weight:600;font-size:4.5px;padding:1px 8px}
.foot-bar{position:absolute;left:0;bottom:0;width:100%;height:16px;background:#0c0c0c;font-size:4.3px;color:#888;text-align:center;line-height:16px}
.callbox{position:absolute;right:16px;top:10px;display:flex;align-items:center;gap:4px;background:var(--green);color:var(--ink);font-weight:800;font-size:6px;padding:4px 8px}
.banner{top:20px;height:104px}
.banner h2{position:absolute;width:100%;text-align:center;color:#fff;font-size:15px;top:32px}
.contact-line{display:flex;align-items:center;gap:6px;margin-bottom:10px;font-size:5px;font-weight:600}
.contact-line b{width:14px;height:14px;background:var(--green);display:flex;align-items:center;justify-content:center;font-size:7px}
.label{font-size:4.5px;color:#777;margin-bottom:2px}
.input{height:12px;border:1px solid #ddd;margin-bottom:5px}
</style>
</head>
<body>

<section class="page page-home">
  <nav class="nav"><span class="brand"><i></i>VELKRIN</span><ul><li>Home</li><li>About</li><li>Capabilities</li><li>Products</li><li>Gallery</li><li>Contact</li></ul><span class="btn">SHOP</span></nav>
  <div class="sec hero">
    <div class="photo ph-dark" role="img" aria-label="Close-up of machined black steel rings" style="inset:0"></div>
    <div class="hero-title"><h1>WELCOME TO<span>VELKRIN</span>MANUFACTURING</h1></div>
    <svg class="slant" style="bottom:-1px" width="376" height="30" viewBox="0 0 376 30"><polygon points="0,30 376,0 376,30" fill="#fff"/></svg>
  </div>
  <div class="sec" style="top:200px;height:210px">
    <div class="photo ph-gold" role="img" aria-label="Precision-machined brass parts on a dark surface" style="left:50px;top:30px;width:120px;height:150px"></div>
    <div style="position:absolute;left:190px;top:62px;width:160px">
      <h2>WHY VELKRIN <em>MANUFACTURING?</em></h2>
      <p style="margin-top:6px">Premium parts built in Minnesota for machinists who demand accuracy on every run. Made in USA, always.</p>
    </div>
  </div>
  <div class="sec" style="top:410px;height:180px">
    <h2 style="position:absolute;left:20px;top:60px">WHAT WE DO</h2>
    <div style="position:absolute;left:108px;top:30px;display:flex;gap:6px">
      <div class="card"><b></b><p><strong>Precision CNC</strong>Tight tolerance work for demanding shops.</p></div>
      <div class="card"><b></b><p><strong>Workholding</strong>Tools that keep your setups secure.</p></div>
      <div class="card"><b></b><p><strong>Custom Builds</strong>Parts made to your exact drawing.</p></div>
    </div>
  </div>
  <div class="sec" style="top:590px;height:230px">
    <svg style="position:absolute;left:0;top:0" width="376" height="230" viewBox="0 0 376 230"><polygon points="0,20 190,0 120,230 0,230" fill="#59ff00"/></svg>
    <div class="photo ph-green" role="img" aria-label="Green TARN LOCK clamp with tool bit" style="left:20px;top:40px;width:146px;height:130px"></div>
    <div style="position:absolute;left:196px;top:62px;width:156px">
      <h2>HOW WE MAKE IT <em>BETTER</em></h2>
      <p style="margin-top:6px">The TARN LOCK locks your workpiece fast and holds it firm, so every cut stays true and every setup saves time.</p>
      <span class="btn" style="margin-top:8px">LEARN MORE</span>
    </div>
  </div>
  <div class="sec dark" style="top:820px;height:260px;background:var(--char)">
    <svg class="slant" style="top:-1px" width="376" height="24" viewBox="0 0 376 24"><polygon points="0,0 376,0 0,24" fill="#fff"/></svg>
    <h2 class="center" style="top:40px;color:#fff">OUR CAPABILITIES</h2>
    <div style="position:absolute;left:30px;top:72px;width:316px;display:grid;grid-template-columns:repeat(4,1fr);gap:22px 10px">
      <div class="cap"><b></b>CNC Milling</div><div class="cap"><b></b>CNC Turning</div><div class="cap"><b></b>Grinding</div><div class="cap"><b></b>Wire EDM</div>
      <div class="cap"><b></b>Inspection</div><div class="cap"><b></b>Assembly</div><div class="cap"><b></b>Finishing</div><div class="cap"><b></b>Prototyping</div>
    </div>
    <p class="center" style="top:150px">Every part checked, every order shipped from our Minnesota shop.</p>
    <svg class="slant" style="bottom:-1px" width="376" height="30" viewBox="0 0 376 30"><polygon points="0,0 376,30 0,30" fill="#fff"/></svg>
  </div>
  <div class="sec" style="top:1080px;height:230px">
    <div style="position:absolute;left:22px;top:60px;width:150px">
      <h2>ABOUT US <em>VELKRIN MANUFACTURING</em></h2>
      <p style="margin-top:6px">A family-run Minnesota shop that builds premium tools with one goal: helping machinists do their best work.</p>
      <span class="btn" style="margin-top:8px">READ MORE</span>
    </div>
    <div class="photo ph-steel" role="img" aria-label="Pile of machined steel components" style="left:196px;top:20px;width:156px;height:196px"></div>
    <div class="photo ph-green" role="img" aria-label="TARN LOCK product render" style="left:178px;top:110px;width:64px;height:92px"></div>
  </div>
  <div class="sec" style="top:1310px;height:210px">
    <h2 class="center" style="top:20px">OUR GALLERY</h2>
    <div class="thumbs" style="top:46px;grid-template-columns:repeat(4,1fr);grid-auto-rows:110px">
      <div class="ph-gold" role="img" aria-label="Brass fittings"></div><div class="ph-steel" role="img" aria-label="Steel plate with drilled holes"></div><div class="ph-dark" role="img" aria-label="Machined rings"></div><div class="ph-metal" role="img" aria-label="Aluminium parts"></div>
    </div>
    <div class="center" style="top:170px"><span class="btn">VIEW ALL</span></div>
  </div>
  <footer class="footer" style="top:1530px;height:142px">
    <div class="foot-cols" style="top:22px">
      <div><span class="brand" style="color:#fff"><i></i>VELKRIN</span><p>Premium precision tools, proudly made in USA.</p></div>
      <div><h3>LINKS</h3>Home<br>About Us<br>Capabilities<br>Shop<br>Contact</div>
      <div><h3>CONTACT</h3>(612) 555-0187<br>hello@velkrin.example<br>4120 Birchline Ave<br>Elmvale, MN</div>
      <div><h3>NEWSLETTER</h3>Get product news.<div class="field"></div><span class="send">SUBMIT</span></div>
    </div>
    <div class="foot-bar">© Velkrin Manufacturing. All rights reserved.</div>
  </footer>
</section>

<section class="page page-gallery">
  <nav class="nav"><span class="brand"><i></i>VELKRIN</span><ul><li>Home</li><li>About</li><li>Products</li><li>Gallery</li><li>Contact</li></ul><span class="btn">SHOP</span></nav>
  <div class="sec banner">
    <div class="photo ph-dark" role="img" aria-label="Rows of machined metal parts" style="inset:0"></div>
    <h2>GALLERY</h2>
    <svg class="slant" style="bottom:-1px" width="376" height="30" viewBox="0 0 376 30"><polygon points="0,30 376,0 376,8 30,30" fill="#59ff00"/><polygon points="40,30 376,10 376,30" fill="#fff"/></svg>
  </div>
  <h2 class="center" style="top:146px">OUR PROJECTS</h2>
  <div class="thumbs" style="top:170px;grid-template-columns:repeat(4,1fr);grid-auto-rows:96px">
    <div class="ph-gold" role="img" aria-label="Brass parts"></div><div class="ph-steel" role="img" aria-label="Steel plate"></div><div class="ph-metal" role="img" aria-label="Machined housings"></div><div class="ph-dark" role="img" aria-label="Black bolts"></div>
    <div class="ph-steel" role="img" aria-label="Perforated sheet"></div><div class="ph-dark" role="img" aria-label="Stacked rings"></div><div class="ph-gold" role="img" aria-label="Copper fittings"></div><div class="ph-metal" role="img" aria-label="Turned shafts"></div>
  </div>
  <div class="center" style="top:388px"><span class="btn">LOAD MORE</span></div>
  <footer class="footer" style="top:488px;height:160px">
    <div class="callbox">☎ (612) 555-0187</div>
    <div class="foot-cols" style="top:40px">
      <div><span class="brand" style="color:#fff"><i></i>VELKRIN</span><p>Premium precision tools, proudly made in USA.</p></div>
      <div><h3>LINKS</h3>Home<br>About Us<br>Capabilities<br>Shop<br>Contact</div>
      <div><h3>CONTACT</h3>(612) 555-0187<br>hello@velkrin.example<br>4120 Birchline Ave<br>Elmvale, MN</div>
      <div><h3>NEWSLETTER</h3>Get product news.<div class="field"></div><span class="send">SUBMIT</span></div>
    </div>
    <div class="foot-bar">© Velkrin Manufacturing. All rights reserved.</div>
  </footer>
</section>

<section class="page page-product">
  <nav class="nav"><span class="brand"><i></i>VELKRIN</span><ul><li>Home</li><li>About</li><li>Products</li><li>Gallery</li><li>Contact</li></ul><span class="btn">SHOP</span></nav>
  <div class="sec banner">
    <div class="photo ph-steel" role="img" aria-label="Heap of machined steel parts" style="inset:0"></div>
    <h2>PRODUCT</h2>
    <svg class="slant" style="bottom:-1px" width="376" height="30" viewBox="0 0 376 30"><polygon points="0,30 376,0 376,8 30,30" fill="#59ff00"/><polygon points="40,30 376,10 376,30" fill="#fff"/></svg>
  </div>
  <h2 class="center" style="top:140px">PRODUCT INFO</h2>
  <div class="row" style="top:166px;height:190px">
    <div class="photo ph-green" role="img" aria-label="TARN LOCK clamp, top view" style="left:24px;top:8px;width:150px;height:170px"></div>
    <div style="position:absolute;left:190px;top:20px;width:166px">
      <h3 style="font-size:8px;font-weight:800">TARN LOCK</h3>
      <div class="price">$189.00</div>
      <div class="spec"><b></b><p>Locks in seconds with one hand.</p></div>
      <div class="spec"><b></b><p>Hardened steel body, built to last.</p></div>
      <div class="spec"><b></b><p>Fits standard vise jaws and plates.</p></div>
      <div class="spec"><b></b><p>Made in USA in Minnesota.</p></div>
      <span class="btn btn-green" style="margin-top:4px">BUY NOW</span>
    </div>
  </div>
  <div class="row dark" style="top:366px;height:200px;background:var(--char)">
    <div style="position:absolute;left:24px;top:56px;width:170px">
      <h3 style="font-size:8px;font-weight:800;color:#fff;margin-bottom:8px">BUILT FOR <span style="color:var(--green)">SHOPS</span></h3>
      <div class="spec"><b></b><p>Repeatable clamping force every time.</p></div>
      <div class="spec"><b></b><p>Low profile for full tool access.</p></div>
      <div class="spec"><b></b><p>Corrosion-resistant green finish.</p></div>
    </div>
    <div class="photo ph-green" role="img" aria-label="TARN LOCK clamp, side view" style="left:204px;top:16px;width:150px;height:168px"></div>
  </div>
  <div class="row" style="top:576px;height:180px">
    <div class="photo ph-green" role="img" aria-label="TARN LOCK set in a fixture" style="left:24px;top:10px;width:150px;height:160px"></div>
    <div style="position:absolute;left:190px;top:40px;width:166px">
      <h3 style="font-size:8px;font-weight:800;margin-bottom:8px">ORDER <span style="color:var(--green)">TODAY</span></h3>
      <div class="spec"><b></b><p>Sold in single units and shop packs.</p></div>
      <div class="spec"><b></b><p>Lifetime support from our team.</p></div>
      <span class="btn" style="margin-top:4px">ADD TO CART</span>
    </div>
  </div>
  <footer class="footer" style="top:760px;height:160px">
    <div class="callbox">☎ (612) 555-0187</div>
    <div class="foot-cols" style="top:40px">
      <div><span class="brand" style="color:#fff"><i></i>VELKRIN</span><p>Premium precision tools, proudly made in USA.</p></div>
      <div><h3>LINKS</h3>Home<br>About Us<br>Capabilities<br>Shop<br>Contact</div>
      <div><h3>CONTACT</h3>(612) 555-0187<br>hello@velkrin.example<br>4120 Birchline Ave<br>Elmvale, MN</div>
      <div><h3>NEWSLETTER</h3>Get product news.<div class="field"></div><span class="send">SUBMIT</span></div>
    </div>
    <div class="foot-bar">© Velkrin Manufacturing. All rights reserved.</div>
  </footer>
</section>

<section class="page page-contact">
  <nav class="nav"><span class="brand"><i></i>VELKRIN</span><ul><li>Home</li><li>About</li><li>Products</li><li>Gallery</li><li>Contact</li></ul><span class="btn">SHOP</span></nav>
  <div class="sec banner">
    <div class="photo ph-metal" role="img" aria-label="Assorted metal fasteners" style="inset:0"></div>
    <h2>CONTACT</h2>
    <svg class="slant" style="bottom:-1px" width="376" height="30" viewBox="0 0 376 30"><polygon points="0,30 376,0 376,8 30,30" fill="#59ff00"/><polygon points="40,30 376,10 376,30" fill="#fff"/></svg>
  </div>
  <h2 class="center" style="top:142px">GET IN TOUCH</h2>
  <div style="position:absolute;left:24px;top:176px;width:160px">
    <div class="contact-line"><b>☎</b>(612) 555-0187</div>
    <div class="contact-line"><b>✉</b>hello@velkrin.example</div>
    <div class="contact-line"><b>⌖</b>4120 Birchline Ave, Elmvale MN</div>
    <p style="margin-top:4px">Mon–Fri, 7am to 5pm. We answer every message within one business day.</p>
  </div>
  <form style="position:absolute;left:196px;top:170px;width:156px">
    <div class="label">Name</div><div class="input"></div>
    <div class="label">Email</div><div class="input"></div>
    <div class="label">Message</div><div class="input" style="height:30px"></div>
    <span class="btn btn-green" style="display:block;text-align:center">SEND</span>
  </form>
  <div class="photo ph-map" role="img" aria-label="Street map showing the shop location" style="left:24px;top:356px;width:328px;height:150px"></div>
  <footer class="footer" style="top:536px;height:172px">
    <div class="callbox">☎ (612) 555-0187</div>
    <div class="foot-cols" style="top:44px">
      <div><span class="brand" style="color:#fff"><i></i>VELKRIN</span><p>Premium precision tools, proudly made in USA.</p></div>
      <div><h3>LINKS</h3>Home<br>About Us<br>Capabilities<br>Shop<br>Contact</div>
      <div><h3>CONTACT</h3>(612) 555-0187<br>hello@velkrin.example<br>4120 Birchline Ave<br>Elmvale, MN</div>
      <div><h3>NEWSLETTER</h3>Get product news.<div class="field"></div><span class="send">SUBMIT</span></div>
    </div>
    <div class="foot-bar">© Velkrin Manufacturing. All rights reserved.</div>
  </footer>
</section>

</body>
</html>
```